Paraffin Wax Packaging Design for Nail and Beauty Industry

We need an attractive design for the packaging of our new product, Paraffin Wax. Our company is a wholesale beauty/nail supply company that has been selling to nail salons in the US market for 10 years. We currently sell this product that we buy from another company. Now we want to launch our own brand of Paraffin Wax.

Target Market(s)

Retail nail salons in the US market.

Industry/Entity Type

Industry

Font styles to use
Sans Serif

Colors

Designer to choose colors to be used in the design.

Requirements
Must have
• Our logo (attached).
• All information on the "Ingredient List" (attached).
• Design for Clear Packaging so product can show through.
• Design for Package Dimensions of 4.25" x 11" (110cm x 280 cm).
Nice to have
• Picture related to women's skin and or beauty.
• Contrast as in the design of product that we currently sell (attached).

```html
<!DOCTYPE html>
<html lang="en">
<head>
<meta charset="utf-8">
<title>Paraffin Wax Package</title>
<link rel="stylesheet" href="https://fonts.googleapis.com/css2?family=Tinos:wght@400;700&family=Arimo:wght@400&family=Parisienne&display=swap">
<style>
  :root {
    --backdrop: #e6e6e8;
    --white: #ffffff;
    --ink-navy: #1f1f3a;
    --script-violet: #5b3d98;
    --deep-blue: #2c38a2;
    --soft-blue: #6f7ee0;
    --pale-blue: #b9c3f2;
    --skin-light: #f3e3d8;
    --skin-mid: #e3c0ac;
  }
  * { margin: 0; padding: 0; box-sizing: border-box; }
  html, body { width: 1200px; height: 2400px; overflow: hidden; background: var(--backdrop); }
  .package {
    position: absolute; left: 80px; top: 20px;
    width: 1040px; height: 2360px;
    background: var(--white);
    overflow: hidden;
    box-shadow: 0 10px 30px rgba(0,0,0,0.25);
  }
  .hero-photo {
    position: absolute; left: 0; top: 0; width: 100%; height: 800px;
    background: radial-gradient(ellipse at 50% 45%, var(--skin-mid) 0%, var(--skin-light) 45%, var(--white) 80%);
  }
  .brand {
    position: absolute; left: 0; top: 850px; width: 100%; text-align: center;
    font-family: "Tinos", serif; color: var(--ink-navy);
  }
  .brand-name { font-size: 130px; font-weight: 400; line-height: 1; white-space: nowrap; }
  .brand-tagline {
    display: block; font-size: 34px; line-height: 1; margin: 8px 270px 0 0; text-align: right;
  }
  .product-name {
    position: absolute; left: 0; top: 1110px; width: 100%; text-align: center;
    font-family: "Parisienne", cursive; font-size: 150px; line-height: 1.2;
    color: var(--script-violet); white-space: nowrap;
  }
  .blue-field { position: absolute; left: 0; top: 1340px; width: 100%; height: 1020px; }
  .info {
    position: absolute; left: 0; top: 1610px; width: 100%;
    text-align: center; color: var(--white); font-family: "Tinos", serif;
  }
  .compat { font-weight: 700; font-size: 68px; line-height: 1.12; }
  .benefit { font-size: 40px; line-height: 1.3; margin-top: 26px; }
  .ingredients-title { font-weight: 700; font-size: 30px; line-height: 1.2; margin-top: 22px; }
  .ingredients { font-size: 26px; line-height: 1.35; margin-top: 4px; }
  .caution-band {
    position: absolute; left: 0; top: 2140px; width: 100%; height: 220px;
    background: var(--deep-blue);
    text-align: center; color: var(--white); font-family: "Arimo", sans-serif;
  }
  .caution { font-size: 30px; line-height: 1.3; padding-top: 18px; }
  .net-weight { font-size: 40px; line-height: 1.2; margin-top: 22px; }
</style>
</head>
<body>
<div class="package">
  <div class="hero-photo" role="img" aria-label="Photo of a woman's hands and feet with violet painted nails"></div>

  <div class="brand">
    <div class="brand-name">By Lumera</div>
    <span class="brand-tagline">Be Radiant</span>
  </div>

  <div class="product-name">Paraffin Wax</div>

  <svg class="blue-field" viewBox="0 0 1040 1020" preserveAspectRatio="none" aria-hidden="true">
    <defs>
      <linearGradient id="fieldGrad" x1="0" y1="0" x2="0" y2="1">
        <stop offset="0" stop-color="#4b58cc"/>
        <stop offset="1" stop-color="#2f3ba8"/>
      </linearGradient>
    </defs>
    <path d="M0 60 C260 -10 520 10 760 50 C880 70 980 60 1040 40 L1040 1020 L0 1020 Z" fill="var(--pale-blue)"/>
    <path d="M0 110 C260 40 540 50 760 90 C880 110 980 100 1040 80 L1040 1020 L0 1020 Z" fill="var(--soft-blue)"/>
    <path d="M0 160 C280 90 540 110 760 150 C880 170 980 160 1040 140 L1040 1020 L0 1020 Z" fill="var(--white)"/>
    <path d="M0 200 C280 130 540 150 760 190 C880 210 980 200 1040 180 L1040 1020 L0 1020 Z" fill="url(#fieldGrad)"/>
  </svg>

  <div class="info">
    <p class="compat">Compatible For Use With<br>Most Wax Paraffin<br>Heat Therapy Units.</p>
    <p class="benefit">Deeply Moisturizes the Skin Restoring a<br>Healthier Look and Feel to Skin.</p>
    <p class="ingredients-title">Ingredients:</p>
    <p class="ingredients">Paraffin waxes and Hydrocarbon waxes, Petrolatum, Paraffin oils,<br>Apricot kernel oil, Fragrance D &amp; C dyes.</p>
  </div>

  <div class="caution-band">
    <p class="caution">Caution:<br>Paraffin is flammable. Do not use near<br>open flame or an unprotected resistance heater.</p>
    <p class="net-weight">Net Wt. 1 lb. (450 g.)</p>
  </div>
</div>
</body>
</html>
```